Cafe - A FRAME Design

Need to create an A frame for my café.
Logo available
Word document - has basic information we think would be good.

Name: Wuzzop Café

Notes from the A-frame printers.
File Requirements
• PDF without trim, crop or registration marks
• All files to be CMYK, not RGB
• All fonts converted to outlines (paths/curves)
• Embed all images and elements
• Files to be 100% scale unless otherwise specified
• 10mm Bleed
Resolution
• Bitmap images no less than 130 DPI at full size
Pantone Colours
• If required Pantone colours must be supplied

Target Market(s)

Mainly Students - University cafe

Requirements
Must have
• Cafe name: Wuzzop
Nice to have
• Might be nice to have background - that orange color same as logo - just an idea

Word document - has basic idea regarding text that should be included

```html
<!DOCTYPE html>
<html lang="en">
<head>
<meta charset="utf-8">
<title>Wuzzop Café – A-Frame Sign</title>
<link href="https://fonts.googleapis.com/css2?family=Rajdhani:wght@700&family=Poppins:wght@400;500;700&display=swap" rel="stylesheet">
<style>
  :root {
    --orange: #e8592b;
    --charcoal: #3b3c40;
    --paper: #ffffff;
    --sketch-soft: #f1edea;
    --sketch-light: #e6dfda;
    --sketch-mid: #d5cac2;
    --sketch-brown: #bfae a2;
    --sketch-deep: #a8958a;
  }
  * { margin: 0; padding: 0; box-sizing: border-box; }
  html, body { width: 800px; height: 1200px; overflow: hidden; background: var(--paper); }
  .sign {
    position: relative;
    width: 800px;
    height: 1200px;
    background: var(--paper);
    overflow: hidden;
    font-family: "Poppins", sans-serif;
    color: var(--charcoal);
  }

  /* Brand */
  .brand {
    position: absolute;
    top: 74px;
    left: 0;
    width: 100%;
    display: flex;
    justify-content: center;
    align-items: center;
    gap: 24px;
  }
  .brand-dot {
    width: 80px;
    height: 80px;
    border-radius: 50%;
    background: var(--orange);
  }
  .brand-name {
    font-weight: 500;
    font-size: 62px;
    line-height: 1;
    letter-spacing: -1px;
    color: var(--charcoal);
  }

  /* Headline */
  .headline {
    position: absolute;
    top: 226px;
    left: 0;
    width: 100%;
    padding-left: 30px;
    text-align: center;
    font-family: "Rajdhani", sans-serif;
    font-weight: 700;
    text-transform: uppercase;
    line-height: 1.06;
  }
  .headline-line { display: block; font-size: 54px; letter-spacing: 0; }
  .headline .accent { color: var(--orange); }
  .headline-feature {
    display: block;
    font-size: 86px;
    line-height: 1;
    color: var(--orange);
    letter-spacing: 1px;
    margin-top: 4px;
  }

  /* Offer list */
  .offers {
    position: absolute;
    top: 474px;
    left: 184px;
    list-style: none;
  }
  .offer {
    display: flex;
    align-items: flex-start;
    height: 77px;
  }
  .offer-icon {
    flex: none;
    width: 62px;
    height: 62px;
    border-radius: 50%;
    background: var(--orange);
    display: flex;
    align-items: center;
    justify-content: center;
  }
  .offer-icon svg { width: 36px; height: 36px; }
  .offer-rule {
    flex: none;
    width: 3px;
    height: 48px;
    margin: 7px 22px 0 22px;
    background: var(--orange);
  }
  .offer-text {
    font-size: 29px;
    font-weight: 400;
    line-height: 42px;
    padding-top: 10px;
    color: var(--charcoal);
  }

  /* Sketch illustration spots */
  .sketch {
    position: absolute;
    border-radius: 50%;
    background: radial-gradient(closest-side, var(--sketch-light) 0%, var(--sketch-soft) 60%, rgba(241,237,234,0) 100%);
  }
  .sketch--warm {
    background: radial-gradient(closest-side, var(--sketch-mid) 0%, var(--sketch-light) 55%, rgba(230,223,218,0) 100%);
  }
  .sketch--deep {
    background: radial-gradient(closest-side, var(--sketch-deep) 0%, var(--sketch-mid) 45%, rgba(213,202,194,0) 100%);
  }
  .sketch-salt      { left: -20px; top: 356px; width: 100px; height: 90px; }
  .sketch-lemon     { left: -22px; top: 472px; width: 96px;  height: 94px; }
  .sketch-pancakes  { left: -20px; top: 590px; width: 178px; height: 130px; }
  .sketch-croissant { left: -18px; top: 744px; width: 110px; height: 104px; }
  .sketch-toast     { left: 748px; top: 326px; width: 80px;  height: 110px; }
  .sketch-greens    { left: 722px; top: 466px; width: 100px; height: 210px; }
  .sketch-beans     { left: 712px; top: 644px; width: 100px; height: 186px; }
  .sketch-sack      { left: 676px; top: 806px; width: 150px; height: 210px; }
  .sketch-mug       { left: -18px; top: 866px; width: 170px; height: 180px; }
  .sketch-leaves    { left: 160px; top: 960px; width: 360px; height: 100px; }
  .sketch-cup       { left: 500px; top: 920px; width: 270px; height: 140px; }

  /* Footer band */
  .footer-band {
    position: absolute;
    left: 0; bottom: 0;
    width: 800px; height: 170px;
  }
  .location {
    position: absolute;
    left: 0; bottom: 40px;
    width: 100%;
    text-align: center;
    font-weight: 700;
    font-size: 52px;
    color: var(--paper);
    letter-spacing: -0.5px;
  }
</style>
</head>
<body>
<main class="sign">

  <header class="brand">
    <span class="brand-dot"></span>
    <span class="brand-name">wuzzop</span>
  </header>

  <div class="sketch sketch-salt" role="img" aria-label="Line sketch of a salt shaker"></div>
  <div class="sketch sketch-lemon" role="img" aria-label="Line sketch of a lemon slice"></div>
  <div class="sketch sketch-pancakes" role="img" aria-label="Line sketch of a pancake stack with berries"></div>
  <div class="sketch sketch-croissant" role="img" aria-label="Line sketch of a croissant"></div>
  <div class="sketch sketch-toast" role="img" aria-label="Line sketch of a slice of toast"></div>
  <div class="sketch sketch-greens" role="img" aria-label="Line sketch of a herb sprig and bacon strips"></div>
  <div class="sketch sketch--warm sketch-beans" role="img" aria-label="Sketched scattered coffee beans"></div>

  <h1 class="headline">
    <span class="headline-line">Your <span class="accent">Environmentally</span></span>
    <span class="headline-line">&amp; Sustainability</span>
    <span class="headline-feature">Focused Café</span>
  </h1>

  <ul class="offers">
    <li class="offer">
      <span class="offer-icon">
        <svg viewBox="0 0 36 36" fill="none" stroke="#fff" stroke-width="2" stroke-linecap="round">
          <path d="M8 16h18v5a7 7 0 0 1-7 7h-4a7 7 0 0 1-7-7z"/>
          <path d="M26 18h2a3 3 0 0 1 0 6h-3"/>
          <path d="M6 31h24"/>
          <path d="M13 6c-2 2 2 4 0 7M18 6c-2 2 2 4 0 7M23 6c-2 2 2 4 0 7"/>
        </svg>
      </span>
      <span class="offer-rule"></span>
      <span class="offer-text">Specialty Coffee</span>
    </li>
    <li class="offer">
      <span class="offer-icon">
        <svg viewBox="0 0 36 36" fill="none" stroke="#fff" stroke-width="2" stroke-linejoin="round">
          <rect x="8" y="16" width="18" height="14" rx="2"/>
          <path d="M8 21h18M8 25h18"/>
          <path d="M10 16l3-8h8l3 8"/>
          <path d="M23 8l3-3"/>
        </svg>
      </span>
      <span class="offer-rule"></span>
      <span class="offer-text">Fresh Food</span>
    </li>
    <li class="offer">
      <span class="offer-icon">
        <svg viewBox="0 0 36 36" fill="none" stroke="#fff" stroke-width="2" stroke-linejoin="round">
          <path d="M9 18a9 7 0 0 1 18 0z"/>
          <path d="M10 18l2 12h12l2-12"/>
          <path d="M15 19l1 11M21 19l-1 11"/>
          <circle cx="18" cy="8" r="2"/>
        </svg>
      </span>
      <span class="offer-rule"></span>
      <span class="offer-text">Pastries &amp; Drinks</span>
    </li>
    <li class="offer">
      <span class="offer-icon">
        <svg viewBox="0 0 36 36" fill="none" stroke="#fff" stroke-width="2" stroke-linecap="round">
          <path d="M7 24a11 11 0 0 1 22 0z"/>
          <path d="M5 28h26"/>
          <circle cx="18" cy="11" r="1.5"/>
        </svg>
      </span>
      <span class="offer-rule"></span>
      <span class="offer-text">Catering Available</span>
    </li>
    <li class="offer">
      <span class="offer-icon">
        <svg viewBox="0 0 36 36" fill="none" stroke="#fff" stroke-width="2" stroke-linecap="round" stroke-linejoin="round">
          <path d="M8 28C8 16 16 8 28 8c0 12-8 20-20 20z"/>
          <path d="M8 28L22 14"/>
          <path d="M15 21h-5M19 17v-5"/>
        </svg>
      </span>
      <span class="offer-rule"></span>
      <span class="offer-text">(Vegan &amp; GF) options<br>available</span>
    </li>
  </ul>

  <div class="sketch sketch-mug" role="img" aria-label="Line sketch of a coffee mug with rising steam"></div>
  <div class="sketch sketch--warm sketch-leaves" role="img" aria-label="Sketched leaves and coffee beans"></div>
  <div class="sketch sketch--deep sketch-sack" role="img" aria-label="Engraved-style sack spilling coffee beans"></div>
  <div class="sketch sketch--deep sketch-cup" role="img" aria-label="Engraved-style cup of coffee on a saucer"></div>

  <svg class="footer-band" viewBox="0 0 800 170" preserveAspectRatio="none" aria-hidden="true">
    <path d="M0 22 Q400 -8 800 12 L800 170 L0 170 Z" fill="#3b3c40"/>
    <path d="M0 34 Q400 4 800 24 L800 170 L0 170 Z" fill="#e8592b"/>
  </svg>
  <p class="location">Located @ Building 418</p>

</main>
</body>
</html>
```